Business card design for modern PanoWalk agency

Hello,

I need a business card design for my company Kites7Market.
We mainly offer Zorvex PanoWalk Tours (360° Photography) and it should be a business card with following details:

Name: Tobias Wendler
Number: +49 176 58 20 917
Mail: tobias@kites7market.com
website: kites7market.com

Main colour that we use is the red of the logo.
It´s also important to integrate the "Zorvex Verified logo" as the person on this business card is a Zorvex verified photographer.

And if possible we would also like to integrate something like send us a sms or whatsapp and we call you back. As the number is german but we sell now in Vienna, Austria.

We offer a good price but very high photography quality, as we are mostly students - that´s our concept.

Maybe an idea is to integrate something 360° on the back-side of the card, for example the photo attached (just an idea) or some great design.
See flyer (attached) and kites7market.com for inspiration, maybe use of the photo of me (attached) in a circle or something

I´m very excited for your designs and thanks a lot in advance!! :)

Target Market(s)

Shops, hotels, shopping centers, etc. in Vienna, Austria

Industry/Entity Type

Business

Contact Information for Business Card

double-sided, use red of the logo, 360° zorvex pano walk certified photographer

Font styles to use
Serif
Sans Serif

Colors
ec1f27

Requirements
Nice to have
• maybe some 360° design on back-side
• maybe include photo of me in a circle or something or sketched in red colour

```html
<!DOCTYPE html>
<html lang="en">
<head>
<meta charset="utf-8">
<title>Kites7Market business card</title>
<link rel="stylesheet" href="https://fonts.googleapis.com/css2?family=Ubuntu:wght@400;500;700&display=swap">
<style>
  :root {
    --brand-red: #e31b3a;
    --ink-grey: #5d5d5d;
    --logo-grey: #8a8a8a;
    --paper: #fcfcfd;
    --backdrop: #ececec;
    --photo-dark: #1d3346;
    --photo-mid: #4f6677;
    --photo-light: #9fb0ba;
    --thumb: #1b3550;
    --verified-green: #2e9b45;
  }
  * { box-sizing: border-box; margin: 0; padding: 0; }
  html, body { width: 1200px; height: 1000px; overflow: hidden; }
  body {
    background: var(--backdrop);
    font-family: "Ubuntu", sans-serif;
    position: relative;
  }
  .card {
    position: absolute;
    width: 560px;
    height: 330px;
    box-shadow: 0 4px 14px rgba(0,0,0,.18);
    overflow: hidden;
  }

  /* Front side */
  .card-front { left: 90px; top: 150px; background: var(--paper); }
  .front-band {
    position: absolute; left: 0; top: 0; bottom: 0; width: 78px;
    background: var(--brand-red);
  }
  .holder-name {
    position: absolute; left: 100px; top: 70px;
    font-size: 30px; font-weight: 700; color: var(--ink-grey);
  }
  .holder-name .surname { color: var(--brand-red); }
  .holder-role {
    position: absolute; left: 102px; top: 112px; width: 280px;
    font-size: 17px; line-height: 1.1; color: var(--ink-grey);
  }
  .contact-list { position: absolute; left: 64px; top: 220px; list-style: none; }
  .contact-list li {
    display: flex; align-items: center; gap: 12px;
    height: 28px; margin-bottom: 6px;
    font-size: 14px; color: var(--ink-grey);
  }
  .contact-icon {
    width: 26px; height: 26px; border-radius: 50%;
    background: var(--paper);
    display: flex; align-items: center; justify-content: center;
  }
  .front-wordmark {
    position: absolute; right: 28px; top: 24px;
    display: flex; flex-direction: column; align-items: center; gap: 12px;
  }
  .wordmark-text {
    writing-mode: vertical-rl; transform: rotate(180deg);
    font-size: 29px; font-weight: 500; letter-spacing: 1px;
    color: var(--logo-grey); line-height: 1;
  }
  .wordmark-square { width: 44px; height: 44px; flex-shrink: 0; background: var(--brand-red); }

  /* Back side */
  .card-back { left: 550px; top: 520px; }
  .back-photo {
    position: absolute; inset: 0;
    background: linear-gradient(135deg, var(--photo-dark) 0%, var(--photo-mid) 45%, var(--photo-light) 60%, var(--photo-dark) 100%);
  }
  .back-tab {
    position: absolute; right: 22px; top: 0; width: 62px; height: 20px;
    background: var(--brand-red);
  }
  .back-wordmark {
    position: absolute; right: 30px; top: 40px;
    display: flex; flex-direction: column; align-items: center; gap: 8px;
  }
  .back-wordmark .wordmark-text { color: #ffffff; font-size: 20px; letter-spacing: 0; }
  .back-wordmark .wordmark-square { width: 26px; height: 26px; background: none; border: 3px solid #ffffff; }
  .viewer-bar {
    position: absolute; left: 0; right: 0; bottom: 0; height: 88px;
    background: rgba(235,238,242,.86);
  }
  .nav-button {
    position: absolute; top: 230px; width: 40px; height: 40px; border-radius: 50%;
    background: var(--brand-red); border: 3px solid #dfe3e8;
    display: flex; align-items: center; justify-content: center;
    box-shadow: 0 2px 4px rgba(0,0,0,.3);
  }
  .nav-prev { left: 158px; }
  .nav-next { left: 358px; }
  .thumb-strip {
    position: absolute; left: 42px; bottom: 18px; display: flex; gap: 4px;
  }
  .thumb { width: 64px; height: 24px; background: var(--thumb); }
  .verified-mark {
    position: absolute; right: 32px; bottom: 20px;
    font-size: 18px; font-weight: 400; color: var(--verified-green);
    text-align: right; line-height: 1.1; white-space: nowrap;
  }
</style>
</head>
<body>

<section class="card card-front" aria-label="Business card front">
  <div class="front-band"></div>
  <h1 class="holder-name">Tobias <span class="surname">Wendler</span></h1>
  <p class="holder-role">360° zorvex pano walk certified photographer</p>
  <ul class="contact-list">
    <li>
      <span class="contact-icon">
        <svg width="14" height="14" viewBox="0 0 24 24"><path fill="#e31b3a" d="M6.6 10.8a15 15 0 0 0 6.6 6.6l2.2-2.2c.3-.3.7-.4 1-.2 1.1.4 2.3.6 3.6.6.6 0 1 .4 1 1V20c0 .6-.4 1-1 1A17 17 0 0 1 3 4c0-.6.4-1 1-1h3.5c.6 0 1 .4 1 1 0 1.3.2 2.5.6 3.6.1.3 0 .7-.2 1z"/></svg>
      </span>
      +49 176 58 20 917
    </li>
    <li>
      <span class="contact-icon">
        <svg width="14" height="14" viewBox="0 0 24 24"><rect x="2" y="5" width="20" height="14" fill="#e31b3a"/><path d="M2 5l10 8 10-8" fill="none" stroke="#fff" stroke-width="2"/></svg>
      </span>
      tobias@kites7market.com
    </li>
    <li>
      <span class="contact-icon">
        <svg width="14" height="14" viewBox="0 0 24 24" fill="none" stroke="#e31b3a" stroke-width="2"><circle cx="12" cy="12" r="10"/><ellipse cx="12" cy="12" rx="4" ry="10"/><path d="M2 12h20"/></svg>
      </span>
      www.kites7market.com
    </li>
  </ul>
  <div class="front-wordmark">
    <span class="wordmark-text">KITES7MARKET</span>
    <span class="wordmark-square"></span>
  </div>
</section>

<section class="card card-back" aria-label="Business card back">
  <div class="back-photo" role="img" aria-label="Aerial 360° photograph of city buildings, a street with parked cars and rooftop pools"></div>
  <div class="back-tab"></div>
  <div class="back-wordmark">
    <span class="wordmark-text">KITES7MARKET</span>
    <span class="wordmark-square"></span>
  </div>
  <div class="viewer-bar"></div>
  <span class="nav-button nav-prev">
    <svg width="14" height="14" viewBox="0 0 24 24"><path d="M15 4l-8 8 8 8" fill="none" stroke="#fff" stroke-width="4"/></svg>
  </span>
  <span class="nav-button nav-next">
    <svg width="14" height="14" viewBox="0 0 24 24"><path d="M9 4l8 8-8 8" fill="none" stroke="#fff" stroke-width="4"/></svg>
  </span>
  <div class="thumb-strip">
    <span class="thumb" role="img" aria-label="Panorama thumbnail"></span>
    <span class="thumb" role="img" aria-label="Panorama thumbnail"></span>
    <span class="thumb" role="img" aria-label="Panorama thumbnail"></span>
    <span class="thumb" role="img" aria-label="Panorama thumbnail"></span>
    <span class="thumb" role="img" aria-label="Panorama thumbnail"></span>
  </div>
  <p class="verified-mark">Zorvex verified</p>
</section>

</body>
</html>
```